New website for gluNote

We are looking to redesign our e-newsletter gluNote. This a monthly newsletter that publishes the latest research and product news in the diabetes field for people with diabetes. Our current website is here: www.glunote.us.

The parameters are the new site must incorporate our logo, must use the same colors (variation in shade and adding some colors is fine, but the initial pallet should stay) and must be in 1024 by 768 px. It is crucially important that the font in the new design be easily readable (dark, well spaced). If it could be a layered PSD that would be ideal. We have attached 2 sketches of our own brainstorming for a potential lay-out for the home and a new issue page, but these are very rough and should not in any way limit the true designers out there.

We're envisioning a very polished, sophisticated looking magazine-esque site that presents a lot of information. When we were brainstorming for new site ideas we looked at major monthly publications such as the Harbor Monthly (www.harbormonthly.com) or Silver Quill (www.sq.com). Like these sites we would still like to feature much of our newest content on the front page, but in a manner that makes good use of space and feels uncluttered. Information needs to be clearly labeled and easy to find. In terms of the overall tone of the website, we do very much want it to be nice and elegant looking site, and one that is targeting a smart, engaged audience.
Updates

Reason: I didn't realize I'd made this due on a Sunday. Please take a couple of extra days everyone.

Industry/Entity Type

News

Requirements
Must have
• The logo. The same color scheme we currently use
Nice to have
• We like the idea of having a featured content box, of using hover buttons on top for our various sections, and potentially using a 3 column setup. However, we are not web designers, so the designer can use these suggestions at their discretion.

```html
<!DOCTYPE html>
<html lang="en">
<head>
<meta charset="utf-8">
<title>gluNote – research and product news for people with diabetes</title>
<link href="https://fonts.googleapis.com/css2?family=Arimo:wght@400;700&family=Libre+Baskerville&display=swap" rel="stylesheet">
<style>
:root{
  --frame:#4a2b1f;
  --page:#ffffff;
  --side:#edebe8;
  --ink:#3a2418;
  --teal-light:#86cbc7;
  --teal:#4fa19c;
  --teal-dark:#1f524f;
  --teal-pale:#cfe9e7;
  --card-edge:#d8d8d8;
  --placeholder:#c6c6c6;
  --pdf-red:#d9141b;
}
*{box-sizing:border-box;margin:0;padding:0}
html,body{width:983px;height:1200px;overflow:hidden}
body{background:var(--frame);font-family:"Arimo",Arial,sans-serif;color:var(--ink);position:relative}
.page{position:absolute;left:21px;top:26px;width:941px;height:1138px;background:var(--page)}
.abs{position:absolute}
.sidebar-bg{left:701px;top:224px;width:240px;height:914px;background:var(--side);border-left:2px solid #dcdad6}

.brand{left:30px;top:28px;font-family:"Libre Baskerville",Georgia,serif;font-size:60px;color:var(--ink);letter-spacing:-2px;line-height:1}
.tagline{left:124px;top:96px;font-family:"Libre Baskerville",Georgia,serif;font-size:14px;color:var(--ink)}
.size-btn{top:54px;width:40px;height:40px;border:1px solid #9a9a9a;border-radius:4px;background:linear-gradient(#fafafa,#d9d9d9);font-size:26px;color:#555;display:flex;align-items:center;justify-content:center}
.size-btn small{font-size:12px}

.nav{left:0;top:146px;width:941px;height:42px;background:linear-gradient(var(--teal-light),var(--teal));display:flex}
.nav a{color:#fff;font-size:12px;font-weight:700;text-decoration:none;display:flex;align-items:center;justify-content:center;border-right:1px solid #3e8d89;height:42px}
.nav a.active{background:var(--teal-dark)}
.search{left:642px;top:7px;width:177px;height:28px;border-radius:14px;background:#fff;font-size:11px;color:#2f6f6b;padding:8px 14px}
.search svg{position:absolute;right:8px;top:6px}
.adv{left:828px;top:7px;width:105px;height:28px;border-radius:14px;background:linear-gradient(#fff,#e4e4e4);font-size:10.5px;color:#444;display:flex;align-items:center;justify-content:center}

.subnav{left:0;top:188px;width:941px;height:36px;background:linear-gradient(#fff,#e6f3f2);border-bottom:1px solid #cfe1df;font-size:10.5px;display:flex;align-items:center}
.subnav span{padding:0 11px;line-height:35px;white-space:nowrap}
.subnav span:first-child{border-right:1px solid #cfe1df;width:104px}

.feature{left:7px;top:246px;width:685px;height:247px;border:1px solid var(--card-edge);border-radius:8px;background:linear-gradient(#fff 55%,#dcdcdc)}
.feature-img{left:6px;top:4px;width:410px;height:238px;border:1px solid var(--card-edge);border-radius:8px;background:#fff;color:#e2e2e2;font-size:22px;display:flex;align-items:center;justify-content:center}
.feature h2{left:446px;top:13px;font-size:19px;font-weight:400}
.feature p{left:446px;width:226px;font-size:11.5px;line-height:17.3px}

.card{width:330px;height:190px;border:1px solid var(--card-edge);border-radius:8px;background:linear-gradient(#fff 60%,#d8d8d8)}
.card .thumb{left:13px;top:16px;width:149px;height:155px;border-radius:8px;background:var(--placeholder);border:1px solid #ddd;color:#fff;font-size:17px;display:flex;align-items:center;justify-content:center}
.card h3{left:176px;top:14px;font-size:19px;font-weight:400;white-space:nowrap}
.card p{left:176px;top:47px;width:142px;font-size:11.5px;line-height:17.3px}
.card .more{right:15px;top:143px;font-size:11.5px;font-weight:700}

.dropdown{left:102px;top:224px;width:190px;height:151px;background:var(--teal-pale);box-shadow:0 2px 6px rgba(0,0,0,.25);display:grid;grid-template-columns:88px 102px;grid-auto-rows:29px;font-size:10.5px}
.dropdown span{display:flex;align-items:center;justify-content:center;border:1px solid #fff}

.join{left:711px;top:245px;width:221px;height:232px;background:linear-gradient(#7cc2be,#4f9d98);border:1px solid #c9dedb;text-align:center;color:#fff}
.join h2{font-size:22px;font-weight:400;line-height:29px;margin-top:24px;text-shadow:0 1px 2px rgba(0,0,0,.35)}
.join .signup{left:13px;top:108px;width:194px;height:113px;border:1px solid #cfe8e6;border-radius:8px;background:linear-gradient(#5aa7a2,#3a8681);font-size:16px;line-height:22px;padding-top:58px}
.join .icon{left:70px;top:8px;width:54px;height:46px;border-radius:4px;background:linear-gradient(#f2f2f2,#c8d6e4)}

.print{left:711px;top:494px;width:221px;height:117px;border:1px solid #c8c8c8;background:linear-gradient(#fff,#dedede)}
.print p{left:12px;top:40px;width:120px;text-align:center;font-size:16px;line-height:24px}

.tabs{left:711px;top:629px;display:flex}
.tabs span{width:64px;height:38px;font-size:10px;line-height:12px;display:flex;align-items:center;justify-content:center;text-align:center;background:var(--teal);color:#fff;border-right:1px solid #8cc7c3}
.tabs span.on{background:#fff;color:var(--ink)}
.tab-panel{left:711px;top:667px;width:221px;height:182px;background:#fff;border:1px solid #d6d6d6;font-size:10px;line-height:18px}
.tab-panel h4{font-size:10.5px;margin-left:10px}
.tab-panel p{margin-left:24px;white-space:nowrap}
.tab-panel .more{right:10px;top:160px;font-size:11.5px;font-weight:700;line-height:1}

.footer{left:0;top:1176px;width:983px;text-align:center;color:#fff;font-size:10px}
</style>
</head>
<body>
<div class="page">
  <div class="abs sidebar-bg"></div>

  <div class="abs brand">gluNote</div>
  <div class="abs tagline">research and product news for people with diabetes</div>
  <div class="abs size-btn" style="left:838px"><small>A</small>A</div>
  <div class="abs size-btn" style="left:884px">A<small>A</small></div>

  <nav class="abs nav">
    <a style="width:85px">Home</a>
    <a class="active" style="width:84px">Issues</a>
    <a style="width:95px">Columns</a>
    <a style="width:82px">Topics</a>
    <a style="width:92px">About Us</a>
    <div class="abs search">Search
      <svg width="16" height="16" viewBox="0 0 16 16"><circle cx="6" cy="6" r="4.5" fill="none" stroke="#555" stroke-width="2"/><line x1="9.5" y1="9.5" x2="14" y2="14" stroke="#555" stroke-width="2.5"/></svg>
    </div>
    <div class="abs adv">Advanced Search</div>
  </nav>

  <div class="abs subnav"><span>CURRENT ISSUE</span><span>ARCHIVES</span></div>

  <section class="abs feature">
    <div class="abs feature-img" role="img" aria-label="Featured story image">FEATURED IMAGE</div>
    <h2 class="abs">Featured Content</h2>
    <p class="abs" style="top:47px">Lorem ipsum dolor siit amet consecutor. Lorem ipsum dolor siit amet consecutor. Lorem ipsum dolor siit amet consecutor. Lorem ipsum dolor siit amet consecutor.</p>
    <p class="abs" style="top:146px">Lorem ipsum dolor siit amet consecutor. Lorem ipsum dolor siit amet consecutor. Lorem ipsum dolor siit amet consecutor. Lorem ipsum dolor siit amet consecutor.</p>
  </section>

  <article class="abs card" style="left:7px;top:509px"><div class="abs thumb" role="img" aria-label="Column image">Image</div><h3 class="abs">From the Editor</h3><p class="abs">Lorem ipsum dolor siit amet consecutor. Lorem ipsum dolor siit amet consecutor. Lorem ipsum dolor siit amet consecutor.</p><span class="abs more">Read More...</span></article>
  <article class="abs card" style="left:362px;top:509px"><div class="abs thumb" role="img" aria-label="Column image">Image</div><h3 class="abs">Learning Curve</h3><p class="abs">Lorem ipsum dolor siit amet consecutor. Lorem ipsum dolor siit amet consecutor. Lorem ipsum dolor siit amet consecutor.</p><span class="abs more">Read More...</span></article>
  <article class="abs card" style="left:7px;top:715px"><div class="abs thumb" role="img" aria-label="Column image">Image</div><h3 class="abs">Sum Musings</h3><p class="abs">Lorem ipsum dolor siit amet consecutor. Lorem ipsum dolor siit amet consecutor. Lorem ipsum dolor siit amet consecutor.</p><span class="abs more">Read More...</span></article>
  <article class="abs card" style="left:362px;top:715px"><div class="abs thumb" role="img" aria-label="Column image">Image</div><h3 class="abs">Trial Watch</h3><p class="abs" style="top:63px">Lorem ipsum dolor siit amet consecutor. Lorem ipsum dolor siit amet consecutor. Lorem ipsum dolor siit amet consecutor.</p><span class="abs more" style="top:160px">Read More...</span></article>
  <article class="abs card" style="left:7px;top:922px"><div class="abs thumb" role="img" aria-label="Column image">Image</div><h3 class="abs">Quotable Quotes</h3><p class="abs">Lorem ipsum dolor siit amet consecutor. Lorem ipsum dolor siit amet consecutor. Lorem ipsum dolor siit amet consecutor.</p><span class="abs more">Read More...</span></article>
  <article class="abs card" style="left:362px;top:922px"><div class="abs thumb" role="img" aria-label="Column image">Image</div><h3 class="abs">Finger Sticks</h3><p class="abs">Lorem ipsum dolor siit amet consecutor. Lorem ipsum dolor siit amet consecutor. Lorem ipsum dolor siit amet consecutor.</p><span class="abs more">Read More...</span></article>

  <div class="abs dropdown">
    <span>2011</span><span>January</span>
    <span>2010</span><span>February</span>
    <span>2009</span><span>March</span>
    <span>2008</span><span>April</span>
    <span>2007</span><span>May</span>
  </div>

  <aside class="abs join">
    <h2>Join the gluNote<br>community!</h2>
    <div class="abs signup">
      <div class="abs icon" role="img" aria-label="Sign-up form icon"></div>
      Sign up for a free<br>subscription here
    </div>
  </aside>

  <aside class="abs print">
    <p class="abs">Print our latest issue here</p>
    <svg class="abs" style="left:136px;top:9px" width="80" height="98" viewBox="0 0 80 98">
      <path d="M2 2 H58 L78 22 V96 H2 Z" fill="#fff" stroke="#bbb"/>
      <path d="M58 2 V22 H78" fill="#e8e8e8" stroke="#bbb"/>
      <rect x="2" y="76" width="76" height="20" fill="var(--pdf-red)"/>
    </svg>
  </aside>

  <div class="abs tabs"><span class="on">Recently<br>Added</span><span>Most<br>Popular</span><span>Editors<br>Picks</span></div>
  <div class="abs tab-panel">
    <h4 style="margin-top:12px">›› Article 1</h4>
    <p style="margin-top:3px">Lorem ipsum dolor siit amet consecutor.<br>Lorem ipsum dolor siit amet dolor.</p>
    <h4 style="margin-top:14px">›› Article 2</h4>
    <p style="margin-top:3px">Lorem ipsum dolor siit amet consecutor.<br>Lorem ipsum dolor siit amet dolor.</p>
    <span class="abs more">More...</span>
  </div>
</div>
<footer class="abs footer">© 2011 gluNote®. All rights reserved.</footer>
</body>
</html>
```